Velk Partners Building Business Cards

We need a business card that reflects our business as "Solar Experts" in San Diego. Browse our website www.velkpartners.example our License needs to be displayed as "CSLB# 3867140" our phone number is (619) 555-0187

Save thousands on your electric bills and increase the value of your home while helping to protect the environment. Our solar installation experts will help you design the system that's right for you, using only the highest quality equipment that will look great and give you ideal performance. Our goal is to make you energy independent, and get your electric bill to 0.

Paul Osterby
(619) 555-0187
paul@velkpartners.example

Target Market(s)

Home owners in san diego looking for solar

Industry/Entity Type

Solar Energy

Contact Information for Business Card

Paul Osterby
(619) 555-0187
paul@velkpartners.example

Font styles to use
Other font styles liked:
• Use our logo font

Requirements
Must have
• License needs to be displayed as "CSLB# 3867140" our phone number is (619) 555-0187
Nice to have
• Real images of rooftop home solar in san diego
Should not have
• our business address

```html
<!DOCTYPE html>
<html lang="en">
<head>
<meta charset="utf-8">
<title>Velk Partners Building – Business Card</title>
<link rel="stylesheet" href="https://fonts.googleapis.com/css2?family=Roboto:wght@400;500;700&display=swap">
<style>
  :root {
    --page-bg: #e7e4df;
    --card-blue-top: #30528f;
    --card-blue-bottom: #26437a;
    --text-light: #eceef3;
    --text-soft: #d6dae6;
    --accent-mauve: #cfa9cf;
    --accent-gold: #d9a02a;
  }
  * { box-sizing: border-box; margin: 0; padding: 0; }
  html, body {
    width: 1200px;
    height: 1200px;
    overflow: hidden;
    background: var(--page-bg);
    font-family: "Roboto", Arial, sans-serif;
  }
  .business-card {
    position: absolute;
    left: 80px;
    top: 291px;
    width: 1040px;
    height: 618px;
    overflow: hidden;
    box-shadow: 0 10px 30px rgba(0, 0, 0, 0.18);
  }
  .card-photo {
    position: absolute;
    inset: 0;
    width: 100%;
    height: 100%;
  }
  .brand {
    position: absolute;
    right: 68px;
    top: 78px;
    display: flex;
    align-items: center;
    gap: 16px;
  }
  .brand-mark {
    width: 26px;
    height: 26px;
    border-radius: 50%;
    background: var(--accent-gold);
  }
  .brand-name {
    font-size: 46px;
    font-weight: 500;
    color: var(--text-light);
    letter-spacing: -0.5px;
    white-space: nowrap;
  }
  .person {
    position: absolute;
    left: 60px;
    top: 336px;
  }
  .person-name {
    font-size: 32px;
    font-weight: 700;
    color: var(--text-light);
  }
  .person-title {
    margin-top: 8px;
    font-size: 23px;
    color: var(--text-soft);
  }
  .contact-list {
    position: absolute;
    left: 60px;
    top: 458px;
    list-style: none;
    font-size: 25px;
    color: var(--text-soft);
  }
  .contact-list li {
    display: flex;
    align-items: center;
    height: 37px;
  }
  .contact-icon {
    width: 26px;
    height: 22px;
    margin-right: 26px;
    flex: none;
  }
  .contact-email .contact-value { color: var(--accent-mauve); }
  .license-number { color: var(--accent-mauve); }
</style>
</head>
<body>
  <div class="business-card">
    <svg class="card-photo" role="img" aria-label="Photo of rooftop solar panels in San Diego, tinted blue" viewBox="0 0 1040 618" preserveAspectRatio="none">
      <defs>
        <linearGradient id="cardTint" x1="0" y1="0" x2="1" y2="1">
          <stop offset="0" stop-color="var(--card-blue-top)"/>
          <stop offset="1" stop-color="var(--card-blue-bottom)"/>
        </linearGradient>
      </defs>
      <rect width="1040" height="618" fill="url(#cardTint)"/>
    </svg>

    <div class="brand">
      <span class="brand-mark"></span>
      <span class="brand-name">Velk Partners Building</span>
    </div>

    <div class="person">
      <p class="person-name">Paul Osterby</p>
      <p class="person-title">Managing Director</p>
    </div>

    <ul class="contact-list">
      <li class="contact-phone">
        <svg class="contact-icon" viewBox="0 0 26 22" aria-hidden="true">
          <path d="M2 7 Q13 0 24 7 L22 10 L18 8 L18 6 Q13 4 8 6 L8 8 L4 10 Z" fill="var(--text-soft)"/>
          <path d="M7 11 L19 11 L22 20 L4 20 Z" fill="var(--text-soft)"/>
        </svg>
        <span class="contact-value">(619) 555-0187</span>
      </li>
      <li class="contact-email">
        <svg class="contact-icon" viewBox="0 0 26 22" aria-hidden="true">
          <rect x="2" y="4" width="22" height="15" fill="none" stroke="var(--text-soft)" stroke-width="2"/>
          <path d="M2 4 L13 13 L24 4" fill="none" stroke="var(--text-soft)" stroke-width="2"/>
        </svg>
        <span class="contact-value">paul@velkpartners.example</span>
      </li>
      <li class="contact-license">
        <span>License: CSLB#&nbsp;<span class="license-number">3867140</span></span>
      </li>
    </ul>
  </div>
</body>
</html>
```